Quillbay.vc needs a better website design!

We need a new and better website for Quillbay.vc. We're a Canadian venture capital firm that invests in innovative entrepreneurs. We compete against the following websites: tormelo.vc, brightvalefund.ca, kestrowvc.com, and dovaran.vc. We're a diverse group of partners and we're dedicated to the founders we invest in.
Updates

I don’t really like stock photos of random people as part of the website design…so please try to stay away from using those images. Thanks, Owen

Target Market(s)

Canadian entrepreneurs and investors

Industry/Entity Type

Venture capital, finance, investment, entrepreneurship

Coding

Coded - Design and coding required

Number of Pages Required

4 page

Font styles to use
Sans Serif

Colors

Designer to choose colors to be used in the design.

Requirements
Must have
• Clean crisp overall design. Fast and to the point.
Nice to have
• Check out www.quillbay.vc - I did it myself and it is too basic and too wordy.
Should not have
• No stock images with random people in them! Not too wordy or with too many large images that are slow to load.

```html
<!DOCTYPE html>
<html lang="en">
<head>
<meta charset="utf-8">
<title>Quillbay.vc</title>
<link href="https://fonts.googleapis.com/css2?family=Poppins:wght@400;500;600&display=swap" rel="stylesheet">
<style>
:root{
  --green:#7a962e;
  --green-dark:#6b8727;
  --ink:#1e2410;
  --text:#2b2b2b;
  --muted:#555;
  --line:#e3e3e3;
  --footer-bg:#f5f5f5;
  --white:#fff;
  --cyan:#1bb8e0;
}
*{margin:0;padding:0;box-sizing:border-box}
html,body{width:1200px;height:2294px;overflow:hidden;background:var(--white);font-family:'Poppins',sans-serif;color:var(--text)}
.page{position:relative;width:1200px;height:2294px}

.site-header{position:absolute;top:0;left:0;width:1200px;height:114px;background:var(--white);border-bottom:1px solid var(--line)}
.brand{position:absolute;left:162px;top:38px;display:flex;align-items:center;gap:8px;color:var(--green);font-weight:600;font-size:20px;letter-spacing:.5px}
.brand-dot{width:26px;height:26px;border-radius:50%;background:var(--green)}
.main-nav{position:absolute;right:165px;top:48px;display:flex;gap:50px;font-size:13.5px;color:#444}
.main-nav a{color:inherit;text-decoration:none;position:relative}
.main-nav a.active{color:var(--green)}
.main-nav a.active::after{content:"";position:absolute;left:-4px;right:-4px;bottom:-6px;height:2px;background:var(--green)}

.hero{position:absolute;top:114px;left:0;width:1200px;height:545px;color:var(--white);text-align:center}
.hero-bg{position:absolute;inset:0;background:linear-gradient(180deg,#5e6a5e 0%,#3f5240 35%,#2c4426 65%,#1f3518 100%)}
.hero-bg::after{content:"";position:absolute;inset:0;background:radial-gradient(ellipse at 50% 60%,rgba(120,140,110,.35),transparent 60%)}
.hero-title{position:absolute;top:118px;left:160px;width:880px;font-size:28.5px;font-weight:500;line-height:46px}
.numbers-label{position:absolute;top:312px;left:262px;width:672px;display:flex;align-items:center;gap:24px;font-size:18px}
.numbers-label::before,.numbers-label::after{content:"";flex:1;height:1px;background:rgba(255,255,255,.35)}
.stats{position:absolute;top:358px;left:334px;display:flex;gap:19px}
.stat{width:165px;height:59px;border:1px solid rgba(255,255,255,.35);display:flex;align-items:center;justify-content:center;gap:8px}
.stat-num{font-size:38px;font-weight:500;line-height:1}
.stat-label{font-size:13.5px;line-height:15px;text-align:left}

.offer{position:absolute;top:659px;left:0;width:1200px}
.section-title{font-size:27px;font-weight:600;color:var(--ink);text-align:center;line-height:42px}
.offer .section-title{position:absolute;top:66px;left:300px;width:600px}
.card{position:absolute;top:186px;width:420px;height:269px;border:1px solid #ddd;border-radius:6px;background:var(--white);box-shadow:0 2px 8px rgba(0,0,0,.06);padding:48px 34px 0}
.card-1{left:162px}.card-2{left:619px}
.card p{margin-top:14px;font-size:19.5px;line-height:32px;color:var(--ink)}

.portfolio{position:absolute;top:1185px;left:0;width:1200px}
.portfolio .section-title{position:absolute;top:14px;left:0;width:1200px}
.logo-grid{position:absolute;top:91px;left:162px;display:grid;grid-template-columns:repeat(5,154px);column-gap:27px;row-gap:22px}
.company{height:67px;border:1px solid #e6e6e6;border-radius:3px;box-shadow:0 1px 4px rgba(0,0,0,.05);display:flex;align-items:center;justify-content:center;gap:7px;font-size:17px;font-weight:600;color:#333}
.company i{width:12px;height:12px;border-radius:50%;background:var(--green);display:block}

.cta{position:absolute;top:1527px;left:0;width:1200px;height:450px;background:linear-gradient(135deg,#7f9b33 0%,#74902a 50%,#6c8826 100%);color:var(--white)}
.cta h2{position:absolute;top:140px;left:207px;font-size:54px;font-weight:500;line-height:64px}
.cta p{position:absolute;top:272px;left:207px;font-size:27px}

.site-footer{position:absolute;top:1977px;left:0;width:1200px;height:271px;background:var(--footer-bg)}
.footer-brand{position:absolute;left:162px;top:180px;color:var(--green);font-size:30px;font-weight:600;letter-spacing:1px;display:flex;align-items:center;gap:10px}
.footer-brand .brand-dot{width:32px;height:32px}
.footer-col{position:absolute;top:60px}
.footer-col h3{font-size:19px;font-weight:500;color:var(--ink);margin-bottom:12px}
.quick{left:544px}
.quick li{list-style:none;font-size:13.5px;line-height:32.5px;color:#333}
.quick li::before{content:"›";margin-right:10px;color:#555}
.contact{left:852px}
.contact .row{font-size:13.5px;display:flex;gap:38px}
.contact .row b{font-weight:500}
.contact h3.follow{margin-top:34px}
.socials{display:flex;gap:7px;margin-top:-2px}
.socials span{width:31px;height:31px;border-radius:50%;background:var(--cyan);display:block}

.copyright{position:absolute;top:2248px;left:0;width:1200px;height:46px;background:var(--green);color:var(--white);font-size:13.5px;display:flex;align-items:center;justify-content:center}
</style>
</head>
<body>
<div class="page">

<header class="site-header">
  <div class="brand"><span class="brand-dot"></span>QUILLBAY.VC</div>
  <nav class="main-nav">
    <a class="active" href="#">Home</a><a href="#">What</a><a href="#">Who</a><a href="#">Portfolio</a>
  </nav>
</header>

<section class="hero">
  <div class="hero-bg" role="img" aria-label="Misty green mountain valley landscape"></div>
  <h1 class="hero-title">Quillbay.vc is a venture capital firm that invests in innovative seed-stage technology companies in Western Canada focused on B2B and SaaS markets.</h1>
  <div class="numbers-label">Quillbay.vc in numbers</div>
  <div class="stats">
    <div class="stat"><span class="stat-num">10</span><span class="stat-label">Portfolio<br>companies</span></div>
    <div class="stat"><span class="stat-num">7</span><span class="stat-label">Follow-on<br>financings</span></div>
    <div class="stat"><span class="stat-num">100</span><span class="stat-label">+<br>Employees</span></div>
  </div>
</section>

<section class="offer">
  <h2 class="section-title">We are serial entrepreneurs and venture capital investors who provide</h2>
  <article class="card card-1">
    <svg width="82" height="76" viewBox="0 0 82 76" fill="none" stroke-width="2.5">
      <g stroke="#888">
        <rect x="2" y="56" width="14" height="18"/><rect x="22" y="42" width="14" height="32"/>
        <rect x="42" y="28" width="14" height="46"/><rect x="62" y="14" width="14" height="60"/>
      </g>
      <path d="M3 32 Q30 26 52 4" stroke="#7a962e"/><path d="M43 4 L53 3 L52 13" stroke="#7a962e"/>
    </svg>
    <p>Mentoring and strategic advice to help you grow your company quickly and efficiently</p>
  </article>
  <article class="card card-2">
    <svg width="76" height="76" viewBox="0 0 76 76" fill="none" stroke-width="2.5">
      <circle cx="48" cy="50" r="22" stroke="#7a962e"/>
      <path d="M55 40 Q48 35 42 40 Q38 47 48 50 Q58 53 54 60 Q48 65 41 60 M48 32 V68" stroke="#7a962e"/>
      <path d="M4 60 V40 Q4 30 18 30 H26" stroke="#888"/>
    </svg>
    <p>Investor introductions to help you raise additional follow-on funding for your startup</p>
  </article>
</section>

<section class="portfolio">
  <h2 class="section-title">Check out our innovative portfolio companies!</h2>
  <div class="logo-grid">
    <div class="company"><i></i>Corvale</div>
    <div class="company">Brenmoor</div>
    <div class="company">Tallowby</div>
    <div class="company">Fennick</div>
    <div class="company">Ostrava</div>
    <div class="company">Pellwick</div>
    <div class="company"><i></i>Quorra</div>
    <div class="company">Haldane Key</div>
    <div class="company">Marrowfield</div>
    <div class="company">Lumetry</div>
  </div>
</section>

<section class="cta">
  <h2>If you have what<br>we're looking for</h2>
  <p>Contact us today</p>
</section>

<footer class="site-footer">
  <div class="footer-brand"><span class="brand-dot"></span>QUILLBAY.VC</div>
  <div class="footer-col quick">
    <h3>Quick Links</h3>
    <ul><li>Home</li><li>What</li><li>Who</li><li>Portfolio</li></ul>
  </div>
  <div class="footer-col contact">
    <h3>Get In Touch</h3>
    <div class="row"><b>Email:</b><span>info@quillbay.vc</span></div>
    <h3 class="follow">Follow Us</h3>
    <div class="socials"><span></span><span></span></div>
  </div>
</footer>

<div class="copyright">Copyright © 2021 Quillbay.vc - All Rights Reserved.</div>

</div>
</body>
</html>
```